Maplecrest Disability - Social Security Disability Attorneys

Our company is expanding to attract clients nationwide for our social security disability practice. We have a logo, but I am looking for a creative and elegant letterhead that projects an image of being technologically advanced but still professional enough for the legal field. I am looking for the "wow factor" combined with this is still professional enough for a law practice.

Requesting letterhead and business card design
Updates

Had to update and change the logo. The previous logo had a typo. Please send updates with the new logo for consideration. The letterhead and business cards should be professional enough to be used for a law firm. Thanks.

Industry/Entity Type

Law Practice, Law Firm, Healthcare Industry, Government

Colors

Designer to choose colors to be used in the design.

Requirements
Nice to have
• **Please create a vertical design for the business card**

```html
<!DOCTYPE html>
<html lang="en">
<head>
<meta charset="utf-8">
<title>Maplecrest Disability – Letterhead</title>
<link href="https://fonts.googleapis.com/css2?family=Tinos:wght@400;700&display=swap" rel="stylesheet">
<style>
  :root{
    --backdrop:#2b2b2d;
    --paper:#ffffff;
    --header-grey:#e6e7ea;
    --brand-blue:#1565c8;
    --brand-blue-light:#2f8fe6;
    --ink:#1c1c1c;
    --footer-ink:#444;
    --decor-grey:#eeeef1;
  }
  html,body{margin:0;padding:0;width:1200px;height:900px;overflow:hidden;background:var(--backdrop);}
  .canvas{position:relative;width:1200px;height:900px;}
  .letterhead{
    position:absolute;left:300px;top:40px;width:600px;height:820px;
    background:var(--paper);overflow:hidden;
    font-family:"Tinos","Times New Roman",serif;color:var(--ink);
  }
  .header-shade{
    position:absolute;left:0;top:0;width:100%;height:150px;
    background:linear-gradient(to bottom,var(--header-grey),var(--paper));
  }
  .header-band{position:absolute;left:0;top:96px;width:600px;height:24px;}
  .brand{position:absolute;right:34px;top:58px;text-align:right;}
  .brand-name{
    font-size:20px;font-weight:700;color:var(--brand-blue);letter-spacing:.5px;
    display:flex;align-items:center;justify-content:flex-end;gap:7px;
  }
  .brand-name .dot{width:9px;height:9px;border-radius:50%;background:var(--brand-blue);}
  .brand-tagline{
    position:absolute;right:34px;top:103px;
    font-size:7.5px;font-weight:700;letter-spacing:2.6px;color:#fff;text-transform:uppercase;
  }
  .recipient{position:absolute;left:62px;top:172px;font-size:12.5px;line-height:15px;display:flex;gap:22px;}
  .salutation{position:absolute;left:62px;top:262px;font-size:12.5px;}
  .body{position:absolute;left:62px;top:292px;width:480px;font-size:12.5px;line-height:15.5px;}
  .body p{margin:0 0 15px;}
  .closing{margin-top:4px;font-size:12.5px;}
  .signature{
    width:170px;height:38px;margin-top:6px;border-radius:3px;
    background:linear-gradient(90deg,rgba(31,42,122,.18),rgba(31,42,122,.06));
  }
  .footer-decor{
    position:absolute;left:0;bottom:0;width:600px;height:130px;
    background:linear-gradient(to bottom,var(--paper),var(--decor-grey));
  }
  .contact{
    position:absolute;right:40px;bottom:34px;
    font-size:9px;line-height:12px;font-style:normal;color:var(--footer-ink);
  }
  .contact b{font-weight:700;}
</style>
</head>
<body>
<div class="canvas">
  <article class="letterhead">
    <div class="header-shade"></div>
    <svg class="header-band" viewBox="0 0 600 24" aria-hidden="true">
      <defs>
        <linearGradient id="bandFill" x1="0" x2="1">
          <stop offset="0" stop-color="#2f8fe6"/>
          <stop offset="1" stop-color="#1565c8"/>
        </linearGradient>
      </defs>
      <path d="M0 2 L600 6 L600 20 L0 14 Z" fill="url(#bandFill)"/>
    </svg>
    <div class="brand">
      <div class="brand-name"><span class="dot"></span>MAPLECREST DISABILITY</div>
    </div>
    <div class="brand-tagline">Social Security Disability Attorneys</div>

    <div class="recipient">
      <span>To:</span>
      <span>Mr./Mrs. Customerand Partner<br>240 Orchard Lane<br>New York<br>NY 10217</span>
    </div>
    <div class="salutation">Dear Customer,</div>
    <div class="body">
      <p>Lorem ipsum dolor sit amet, consetetur sadipscing elitr, sed diam nonumy eirmod tempor invidunt ut labore et dolore magna aliquyam erat, sed diam voluptua. At vero eos et accusam et justo duo dolores et ea rebum. Stet clita kasd gubergren, no sea takimata sanctus est Lorem ipsum dolor sit amet. Lorem ipsum dolor sit amet, consetetur sadipscing elitr, sed diam nonumy eirmod tempor invidunt ut labore et dolore magna aliquyam erat, sed diam voluptua. At vero eos et accusam et justo duo dolores et ea rebum. Stet clita kasd gubergren, no sea takimata sanctus est Lorem ipsum dolor sit amet.</p>
      <p>Duis autem vel eum iriure dolor in hendrerit in vulputate velit esse molestie consequat, vel illum dolore eu feugiat nulla facilisis at vero eros et accumsan et iusto odio dignissim qui blandit praesent luptatum zzril delenit augue duis dolore te feugait nulla facilisi. Lorem ipsum dolor sit amet, consectetuer adipiscing elit, sed diam nonummy nibh euismod tincidunt ut laoreet dolore magna aliquam erat volutpat.</p>
      <p>Nam liber tempor cum soluta nobis eleifend option congue nihil imperdiet doming id quod mazim placerat facer possim assum. Lorem ipsum dolor sit amet, consectetuer adipiscing elit, sed diam nonummy nibh euismod tincidunt ut laoreet dolore magna aliquam erat volutpat. Ut wisi enim ad minim veniam, quis nostrud exerci tation ullamcorper suscipit lobortis nisl ut aliquip ex ea commodo consequat.</p>
      <div class="closing">Sincerely,</div>
      <div class="signature" role="img" aria-label="Handwritten signature in dark blue ink"></div>
    </div>

    <div class="footer-decor" role="img" aria-label="Faint grey swoosh and starburst decoration along the bottom of the page"></div>
    <address class="contact">
      1180 Ridgeview Court<br>
      Atlanta, GA 30318<br>
      <b>P:</b> 404-555-0142<br>
      <b>F:</b> 404-555-0187
    </address>
  </article>
</div>
</body>
</html>
```